TLK Electricial Contracting Services

Hi guys, after a design for my small electrical company, have logo design files to be incorporated into the layout, the basic concept is electrical contracting services for residential, commercial, industrial & data services, image is clean clear and strong,

Card format is to have a nice clean logo on front,with maybe the Residential – commercial – industrial - data, followed with licensed & insured, followed by contact details on backside of the card.

Target Market(s)

Residential, commercial, industrial sectors.

Industry/Entity Type

Electrical

Contact Information for Business Card

TLK logo,
Residential – commercial – industrial - data
REC: 61307
Email: tlk@vornamail.net.au
Phone: 0487 352 019

Requirements
Must have
• Clean & strong design.
Nice to have
• If possible, I would like the logo colours inverted so the text is orange and the background is black on the front of the card, then the backside of the card be the reverse colour
Should not have
• No Sparks, lightning bolts,

```html
<!DOCTYPE html>
<html lang="en">
<head>
<meta charset="utf-8">
<title>TLK Electrical — Business Card</title>
<link rel="stylesheet" href="https://fonts.googleapis.com/css2?family=Saira:wght@700&family=Arimo:wght@400&display=swap">
<style>
  :root {
    --backdrop: #cfd3d3;
    --card-black: #0b0b0b;
    --card-orange: #d9622b;
    --brand-red: #e0321c;
    --ink-black: #0d0d0d;
    --text-light: #d6d6d6;
    --text-muted: #a8a8a8;
    --rule-grey: #8a8a8a;
  }
  * { margin: 0; padding: 0; box-sizing: border-box; }
  html, body {
    width: 1200px; height: 1050px; overflow: hidden;
    background: var(--backdrop);
  }
  .canvas {
    position: relative; width: 1200px; height: 1050px;
    display: flex; align-items: center; justify-content: center; gap: 50px;
  }
  .card {
    position: relative; width: 525px; height: 300px;
    border-radius: 3px; overflow: hidden;
  }
  .card--front { background: var(--card-black); color: var(--text-light); }
  .card--back { background: var(--card-orange); }

  .wordmark {
    font-family: "Saira", sans-serif; font-weight: 700;
    line-height: 1; letter-spacing: 1px;
  }
  .wordmark__name { display: block; }
  .wordmark__line { display: block; letter-spacing: 0.5px; }

  .card--front .wordmark {
    position: absolute; left: 40px; top: 28px; color: var(--brand-red);
  }
  .card--front .wordmark__name { font-size: 62px; }
  .card--front .wordmark__line { font-size: 14px; margin-top: 4px; }

  .divider { position: absolute; left: 0; top: 0; }

  .credentials {
    position: absolute; left: 40px; top: 150px; list-style: none;
    font-family: "Arimo", sans-serif; font-size: 13px; letter-spacing: 1px;
    line-height: 1.7; color: var(--text-muted);
  }

  .services {
    position: absolute; left: 318px; top: 136px; list-style: none;
    font-family: "Arimo", sans-serif; font-size: 15px; letter-spacing: 1px;
    line-height: 1.5;
  }
  .services li:nth-child(2) { margin-left: -10px; }
  .services li:nth-child(3) { margin-left: -20px; }
  .services li:nth-child(4) { margin-left: -30px; }

  .contact {
    position: absolute; right: 40px; bottom: 14px; list-style: none;
    font-family: "Arimo", sans-serif; font-size: 15px; line-height: 1.5;
    text-align: right;
  }
  .contact li { display: flex; align-items: center; justify-content: flex-end; gap: 8px; }
  .contact svg { flex: none; }

  .card--back .wordmark {
    position: absolute; left: 0; right: 0; top: 62px; text-align: center;
    color: var(--ink-black);
  }
  .card--back .wordmark__name { font-size: 132px; }
  .card--back .wordmark__line { font-size: 24px; margin-top: 6px; }
</style>
</head>
<body>
  <main class="canvas">
    <section class="card card--front" aria-label="Card front">
      <div class="wordmark">
        <span class="wordmark__name">TLK</span>
        <span class="wordmark__line">Tobin Lake Electrical</span>
      </div>
      <svg class="divider" width="525" height="300" viewBox="0 0 525 300" aria-hidden="true">
        <polyline points="0,112 240,112 258,126 525,126" fill="none" stroke="var(--rule-grey)" stroke-width="1"/>
        <polyline points="0,106 238,106 250,116" fill="none" stroke="var(--rule-grey)" stroke-width="1"/>
        <line x1="270" y1="238" x2="525" y2="238" stroke="var(--rule-grey)" stroke-width="1"/>
      </svg>
      <ul class="credentials">
        <li>LICENSED &amp; INSURED</li>
        <li>REC: 61307</li>
      </ul>
      <ul class="services">
        <li>RESIDENTIAL</li>
        <li>COMMERCIAL</li>
        <li>INDUSTRIAL</li>
        <li>DATA</li>
      </ul>
      <ul class="contact">
        <li>
          <svg width="12" height="14" viewBox="0 0 12 14" aria-hidden="true"><path d="M2 1h3l1 3-2 1.5c.8 1.8 2 3 3.5 3.5L9 7l3 1v3c0 1-1 2-2 2C5 13 0 8 0 3c0-1 1-2 2-2z" fill="var(--text-light)"/></svg>
          <span>0487 352 019</span>
        </li>
        <li>
          <svg width="16" height="12" viewBox="0 0 16 12" aria-hidden="true"><rect x="0.5" y="0.5" width="15" height="11" fill="none" stroke="var(--text-light)"/><polyline points="0.5,0.5 8,7 15.5,0.5" fill="none" stroke="var(--text-light)"/></svg>
          <span>tlk@vornamail.net.au</span>
        </li>
      </ul>
    </section>

    <section class="card card--back" aria-label="Card back">
      <div class="wordmark">
        <span class="wordmark__name">TLK</span>
        <span class="wordmark__line">Tobin Lake Electrical</span>
      </div>
    </section>
  </main>
</body>
</html>
```